Shopping centre customer engagement software website

We need a multi page site with :

*What we do.
*How it works.
*Benefits
* Case study
* Testimonial
* Business login (we provide link to business portal)
* Consumer login (we provide link to consumer site)
* Book a demo
* Contact us

We want it to be clean and crisp and very self explanatory with little clutter. We are thinking white but are open to what ever looks the best.
Updates

Wordpress is preferred

Need extra days to review

Target Market(s)

Shopping centre managers and retail property companies

Coding

Coded - Design and coding required

Number of Pages Required

5+ page

Font styles to use
Sans Serif

Colors
ffffff

Requirements
Must have
• As listed above and must be responsive! Checkout our existing site for the text to be included (will be edited but it’ll give you an idea) www.vostrelink.com

```html
<!DOCTYPE html>
<html lang="en">
<head>
<meta charset="utf-8">
<title>Vostrelink — Shopping Centre Engagement</title>
<link rel="stylesheet" href="https://fonts.googleapis.com/css2?family=Poppins:wght@300;400;500&family=Montserrat:wght@500;600&display=swap">
<style>
:root{
  --white:#ffffff;
  --ink:#222428;
  --text:#4a4d52;
  --muted:#6b6e73;
  --teal:#6cc5d8;
  --teal-dark:#4fb2c8;
  --hero-a:#7d93c4;
  --hero-b:#8a7fb8;
  --hero-c:#b4a9d6;
  --dark-a:#2b2622;
  --dark-b:#3d362f;
  --footer:#0b0b0c;
  --ring:#9fd6e3;
}
*{box-sizing:border-box;margin:0;padding:0}
html,body{width:1200px;height:3340px;overflow:hidden}
body{position:relative;background:var(--white);font-family:"Poppins",sans-serif;color:var(--text)}
.abs{position:absolute}

/* hero */
.hero{left:0;top:0;width:1200px;height:600px;background:linear-gradient(180deg,var(--hero-a) 0%,var(--hero-b) 55%,var(--hero-c) 100%)}
.brand{left:84px;top:22px;display:flex;align-items:center;gap:12px;color:var(--white);font-family:"Poppins",sans-serif;font-weight:400;font-size:30px;letter-spacing:2px}
.brand-dot{width:40px;height:40px;border-radius:50%;background:#d9dde4}
.nav{right:90px;top:52px;display:flex;gap:40px;font-family:"Montserrat",sans-serif;font-weight:600;font-size:13px;color:var(--white)}
.hero-title{left:0;width:1200px;top:148px;text-align:center;font-size:50px;font-weight:500;color:var(--white)}
.hero-sub{left:0;width:1200px;top:218px;text-align:center;font-family:"Montserrat",sans-serif;font-weight:600;font-size:15px;line-height:24px;color:var(--white)}
.btn-teal{left:508px;top:274px;width:184px;height:48px;background:var(--teal);color:var(--white);font-size:16px;line-height:48px;text-align:center;box-shadow:0 4px 10px rgba(0,0,0,.2)}
.laptop{left:367px;top:367px;width:463px;height:268px;border-radius:14px 14px 4px 4px;background:linear-gradient(180deg,#2a3039,#1b2028 80%,#c9ccd1 80%)}

/* how it works */
.section-title{left:0;width:1200px;text-align:center;font-weight:400;color:var(--ink)}
.hiw-title{top:735px;font-size:32px;letter-spacing:1px}
.hiw-text{left:290px;width:620px;top:782px;text-align:center;font-size:13px;line-height:22px}
.step{width:146px;height:146px;border:2px solid var(--ring);border-radius:50%;background:var(--white)}
.step-icon{position:absolute;left:38px;top:38px;width:66px;height:66px;border-radius:12px}
.step-num{position:absolute;right:-6px;top:-8px;width:40px;height:40px;border-radius:50%;background:var(--ring);color:var(--white);font-size:13px;font-weight:500;line-height:40px;text-align:center}
.step-label{width:200px;text-align:center;font-size:15px;color:var(--ink)}

/* case study */
.case-band{left:0;top:1150px;width:1200px;height:610px}
.case-title{top:1270px;font-size:32px;color:var(--white);font-weight:300}
.case-sub{top:1318px;font-size:22px;color:#d7d7d7;font-weight:300}
.phone-case{left:492px;top:1383px;width:214px;height:432px;border-radius:34px;background:linear-gradient(180deg,#1b1b1d,#2f3033);border:3px solid #8d9097}
.stat{width:84px;height:84px;border-radius:50%;background:var(--white);border:4px solid #1d1d1d;display:flex;align-items:center;justify-content:center;text-align:center;font-size:24px;font-weight:500;color:#111;line-height:24px}
.stat-label{font-size:15px;color:var(--white)}
.stat-label.left{width:300px;text-align:right}
.car{width:34px;height:20px;border-radius:6px;background:#3e6d8c}

/* what we can do */
.wwd-title{top:1865px;font-size:32px}
.wwd-text{left:170px;width:860px;top:1922px;text-align:center;font-size:13px;line-height:22px}
.btn-pill{height:48px;width:160px;border-radius:24px;background:var(--white);color:var(--ink);font-size:15px;line-height:48px;text-align:center;box-shadow:0 4px 14px rgba(0,0,0,.18)}

/* scenario */
.scenario-band{left:0;top:2198px;width:1200px;height:475px}
.scenario-title{left:85px;top:2272px;font-size:22px;color:var(--white);letter-spacing:1px}
.scenario-text{left:85px;top:2320px;width:510px;font-size:13px;line-height:21px;color:var(--white)}
.phone-scenario{left:728px;top:2287px;width:245px;height:300px;border-radius:30px 30px 0 0;background:linear-gradient(180deg,#e9ecf0,#f7f8fa);border:4px solid #b9bcc2}

/* testimonial */
.quote-name{top:2745px;font-size:34px;line-height:44px}
.quote-text{left:255px;width:690px;top:2846px;text-align:center;font-size:13px;line-height:21px}

/* footer */
.footer{left:0;top:3018px;width:1200px;height:260px;background:var(--footer)}
.footer-brand{left:96px;top:3110px;display:flex;align-items:center;gap:12px;color:var(--white);font-size:30px;font-weight:400;letter-spacing:2px}
.f-head{font-size:18px;color:var(--white)}
.f-list{list-style:none;font-size:13px;line-height:24px;color:var(--white)}
.f-list li{display:flex;gap:14px;align-items:flex-start}
.contact li{margin-bottom:14px;line-height:20px}
.links li::before{content:"›";color:#aaa}
.newsletter-input{left:891px;top:3112px;width:222px;height:42px;border:1px solid var(--white);color:#cfcfcf;font-size:13px;line-height:40px;padding-left:18px}
.newsletter-btn{left:891px;top:3167px;width:158px;height:40px;background:var(--teal);color:var(--white);font-size:14px;line-height:40px;text-align:center}
.copyright{left:0;top:3278px;width:1200px;height:62px;background:var(--teal);color:var(--white);font-size:13px;line-height:62px;text-align:center}
</style>
</head>
<body>

<header>
  <div class="abs hero" role="img" aria-label="Shopper walking through a shopping centre, tinted blue-violet"></div>
  <div class="abs brand"><span class="brand-dot"></span>VOSTRELINK</div>
  <nav class="abs nav">
    <span>What We Do</span><span>Benefits</span><span>Testimonials</span><span>How It Works</span><span>Case Study</span><span>Contact</span>
  </nav>
  <h1 class="abs hero-title">Vostrelink</h1>
  <p class="abs hero-sub">Vostrelink exceeds all expectations for Shopping Centre Managers,<br>Shoppers, Tenants and Landlords</p>
  <div class="abs btn-teal">FIND OUT MORE</div>
  <div class="abs laptop" role="img" aria-label="Laptop showing the analytics dashboard"></div>
</header>

<section>
  <h2 class="abs section-title hiw-title">HOW IT WORKS</h2>
  <p class="abs hiw-text">Lorem ipsum dolor sit amet consectetur adipisicing elit sed do eiusmod tempor incididunt ut labore et dolore magna aliqua ut enim ad minim veniam quis nostrud.</p>

  <div class="abs step" style="left:114px;top:873px"><div class="step-icon" role="img" aria-label="Loyalty card icon" style="background:#f3c23c"></div><span class="step-num">01</span></div>
  <div class="abs step" style="left:321px;top:873px"><div class="step-icon" role="img" aria-label="Shop front icon" style="background:#4cb5c9"></div><span class="step-num">02</span></div>
  <div class="abs step" style="left:528px;top:873px"><div class="step-icon" role="img" aria-label="Mobile phone icon" style="background:#5b6f8c"></div><span class="step-num">03</span></div>
  <div class="abs step" style="left:733px;top:873px"><div class="step-icon" role="img" aria-label="Document folder icon" style="background:#f2cf55"></div><span class="step-num">04</span></div>
  <div class="abs step" style="left:940px;top:873px"><div class="step-icon" role="img" aria-label="Presentation chart icon" style="background:#c89a5e"></div><span class="step-num">05</span></div>

  <div class="abs step-label" style="left:87px;top:1026px">Allocate Cards</div>
  <div class="abs step-label" style="left:294px;top:1026px">Direct Marketing</div>
  <div class="abs step-label" style="left:501px;top:1026px">Rewarding Loyalty</div>
  <div class="abs step-label" style="left:706px;top:1026px">Collect Data</div>
  <div class="abs step-label" style="left:913px;top:1026px">Data Analytics</div>
</section>

<section>
  <svg class="abs case-band" viewBox="0 0 1200 610" role="img" aria-label="Blurred shopping centre interior">
    <defs><linearGradient id="caseGrad" x1="0" y1="0" x2="0" y2="1"><stop offset="0" stop-color="#3a332c"/><stop offset="1" stop-color="#24201c"/></linearGradient></defs>
    <polygon points="0,172 802,0 1200,142 1200,610 0,610" fill="url(#caseGrad)"/>
  </svg>
  <h2 class="abs section-title case-title">Case study</h2>
  <p class="abs section-title case-sub">Results from a 31 day campaign</p>
  <div class="abs phone-case" role="img" aria-label="Smartphone showing campaign results screen"></div>

  <div class="abs stat-label left" style="left:67px;top:1421px">VIP Card Holders</div>
  <div class="abs stat" style="left:386px;top:1390px">650</div>
  <div class="abs stat-label left" style="left:67px;top:1548px">Messages Sent</div>
  <div class="abs stat" style="left:386px;top:1517px;font-size:20px">10500</div>
  <div class="abs stat-label left" style="left:67px;top:1675px">Conversion Rate</div>
  <div class="abs stat" style="left:386px;top:1644px">22%</div>

  <div class="abs stat" style="left:728px;top:1390px;font-size:20px;line-height:22px">1.2<br>Hours</div>
  <div class="abs stat-label" style="left:835px;top:1421px">AVG Dwell Time</div>
  <div class="abs stat" style="left:728px;top:1517px"><span class="car" role="img" aria-label="Car icon"></span></div>
  <div class="abs stat-label" style="left:835px;top:1548px">Holding Engagement</div>
  <div class="abs stat" style="left:728px;top:1644px">980</div>
  <div class="abs stat-label" style="left:835px;top:1675px">Loyalty Rewards Issued</div>
</section>

<section>
  <h2 class="abs section-title wwd-title">What we can do for you</h2>
  <div class="abs wwd-text">
    <p>Vostrelink provides shopping centre managers with an easy to use platform which enables them to delight their shoppers, impress their tenants, provide detailed data to their landlords and all accessible to them at the click of button.</p>
    <p style="margin-top:16px">Vostrelink gives shopping centres real time tracking through smart ID's of individual customer journeys through their physical stores, enabling highly targeted, relevant and timely promotional and rewarding capabilities. Furthermore, through deep analytical data processing of the customer journey, centre managers will be able to more accurately and reliably predict shopping behaviours.</p>
  </div>
  <div class="abs btn-pill" style="left:500px;top:2072px">Read More</div>
</section>

<section>
  <svg class="abs scenario-band" viewBox="0 0 1200 475" role="img" aria-label="Blurred view of shoppers inside a mall">
    <defs><linearGradient id="scenGrad" x1="0" y1="0" x2="0" y2="1"><stop offset="0" stop-color="#2a2622"/><stop offset="1" stop-color="#3b3530"/></linearGradient></defs>
    <polygon points="0,0 1200,0 1200,218 400,470 0,330" fill="url(#scenGrad)"/>
  </svg>
  <h3 class="abs scenario-title">EXAMPLE SCENARIO</h3>
  <p class="abs scenario-text">Vostrelink can predict more accurately and more reliably than ever before that on a cold wet Thursday next week: 35% of a retailers customers coming through their doors will be women aged between 30-35 looking to buy kids wear. When they arrive Vostrelink can identify them personally and send them messages based on where they are and their preferences.</p>
  <div class="abs btn-pill" style="left:85px;top:2441px;width:156px">Read More</div>
  <div class="abs phone-scenario" role="img" aria-label="Smartphone showing the reporting dashboard"></div>
</section>

<section>
  <h2 class="abs section-title quote-name">Declan Hale<br>-Riverside Centre Manager</h2>
  <p class="abs quote-text">"All of the data captured has now been analysed, equipping us with invaluable insights into shopping and spending patterns, and the impact of our media campaigns – all of which is gold dust as we plan ahead for future focussed campaigns. The flexibility of the Vostrelink operating platform software means we will most certainly use this system again going forward."</p>
</section>

<footer>
  <div class="abs footer"></div>
  <div class="abs footer-brand"><span class="brand-dot"></span>VOSTRELINK</div>

  <h4 class="abs f-head" style="left:370px;top:3068px;font-weight:400">Contact Info:</h4>
  <ul class="abs f-list contact" style="left:370px;top:3110px;width:280px">
    <li><svg width="12" height="16" viewBox="0 0 12 16"><path d="M6 0a6 6 0 0 0-6 6c0 4.5 6 10 6 10s6-5.5 6-10a6 6 0 0 0-6-6zm0 8.5A2.5 2.5 0 1 1 6 3.5a2.5 2.5 0 0 1 0 5z" fill="#fff"/></svg><span>Vostrelink<br>Unit 7b, Harbour Road<br>Carrowmore, CM12 4RT</span></li>
    <li><svg width="14" height="14" viewBox="0 0 14 14"><path d="M3 0l2.5 3-1.6 1.8a9 9 0 0 0 5.3 5.3L11 8.5 14 11l-1.8 2.6C6 13.5.5 8 .4 1.8z" fill="#fff"/></svg><span>Phone: 0280419375</span></li>
    <li><svg width="14" height="12" viewBox="0 0 14 12"><rect width="14" height="11" y="1" rx="1" fill="#fff"/><path d="M0 2l7 5 7-5" stroke="#0b0b0c" stroke-width="1.3" fill="none"/></svg><span>Email: contact@vostrelink.com</span></li>
  </ul>

  <h4 class="abs f-head" style="left:686px;top:3068px;font-weight:400">Quick Links:</h4>
  <ul class="abs f-list links" style="left:686px;top:3104px">
    <li>What We Do</li><li>Benefits</li><li>Testimonials</li><li>How It Works</li><li>Case Study</li><li>Contact</li>
  </ul>

  <h4 class="abs f-head" style="left:891px;top:3064px;font-weight:400">Newsletter Signup</h4>
  <div class="abs newsletter-input">Email Address</div>
  <div class="abs newsletter-btn">SUBMIT</div>

  <div class="abs copyright">Copyright © 2016. Vostrelink. All rights reserved.</div>
</footer>

</body>
</html>
```